Oil and Gas Exploration and Production company needs a business card design

We need a business card design using our logo and colors in the logo. We want a mainstream design.

```html
<!DOCTYPE html>
<html lang="en">
<head>
<meta charset="UTF-8">
<title>Corvo Oil &amp; Gas – Business Card</title>
<link href="https://fonts.googleapis.com/css2?family=Work+Sans:wght@400;600&display=swap" rel="stylesheet">
<style>
  :root {
    --backdrop: #1b1b1d;
    --card: #222223;
    --card-light: #2c2c2d;
    --gold: #d9a42a;
    --white: #f4f4f2;
  }
  * { margin: 0; padding: 0; box-sizing: border-box; }
  html, body {
    width: 1200px; height: 900px; overflow: hidden;
    background: var(--backdrop);
    font-family: "Work Sans", sans-serif;
  }
  .sheet {
    width: 1200px; height: 900px;
    display: flex; flex-direction: column;
    align-items: center; justify-content: center; gap: 40px;
  }
  .card {
    position: relative;
    width: 720px; height: 405px;
    background: linear-gradient(135deg, var(--card) 0%, var(--card) 55%, var(--card-light) 100%);
    border-bottom: 6px solid var(--gold);
    display: flex; align-items: center;
  }
  .brand {
    display: flex; align-items: center; gap: 14px;
    color: var(--white);
    font-weight: 600;
    font-size: 52px;
    letter-spacing: -0.5px;
    white-space: nowrap;
  }
  .brand-dot {
    width: 38px; height: 38px; border-radius: 50%;
    background: var(--gold); flex: none;
  }
  .card-front { justify-content: center; }
  .card-back { padding-left: 52px; }
  .card-back .brand { font-size: 40px; gap: 12px; }
  .card-back .brand-dot { width: 30px; height: 30px; }
  .divider {
    width: 3px; height: 180px; background: var(--gold);
    margin: 0 36px 0 36px; flex: none;
  }
  .contact { color: var(--white); }
  .contact-name {
    color: var(--gold); font-weight: 600; font-size: 30px; line-height: 1;
  }
  .contact-role {
    font-size: 15px; margin-top: 4px; letter-spacing: 0.5px;
  }
  .contact-address {
    font-size: 16px; line-height: 1.4; margin-top: 18px; font-style: normal;
  }
  .contact-lines { list-style: none; margin-top: 14px; }
  .contact-lines li {
    display: flex; align-items: center; gap: 10px;
    font-size: 16px; line-height: 1.5;
  }
  .contact-lines svg { width: 13px; height: 13px; flex: none; }
  .web-domain { color: var(--gold); }
</style>
</head>
<body>
<main class="sheet">
  <section class="card card-front" aria-label="Card front">
    <div class="brand"><span class="brand-dot"></span>Corvo Oil &amp; Gas</div>
  </section>

  <section class="card card-back" aria-label="Card back">
    <div class="brand"><span class="brand-dot"></span>Corvo Oil &amp; Gas</div>
    <div class="divider"></div>
    <div class="contact">
      <p class="contact-name">Dale Whitmore</p>
      <p class="contact-role">CFO</p>
      <address class="contact-address">2475 W Meridian Ave,<br>Fort Worth, Texas us</address>
      <ul class="contact-lines">
        <li>
          <svg viewBox="0 0 16 16" fill="none" stroke="#d9a42a" stroke-width="1.6"><path d="M4 1.5 L6.5 4.5 5 6.5 Q6.5 9.5 9.5 11 L11.5 9.5 14.5 12 13 14.5 Q6 14 1.5 3 Z"/></svg>
          (555) 014-2290
        </li>
        <li>
          <svg viewBox="0 0 16 16" fill="none" stroke="#d9a42a" stroke-width="1.6"><rect x="1.5" y="3.5" width="13" height="9"/><path d="M1.5 3.5 8 9 14.5 3.5"/></svg>
          info@corvooilgas.com
        </li>
        <li>
          <svg viewBox="0 0 16 16" fill="none" stroke="#d9a42a" stroke-width="1.4"><circle cx="8" cy="8" r="6.5"/><ellipse cx="8" cy="8" rx="3" ry="6.5"/><path d="M1.5 8h13"/></svg>
          <span>www.<span class="web-domain">corvooilgas</span>.com</span>
        </li>
      </ul>
    </div>
  </section>
</main>
</body>
</html>
```